Business Card Design for a new Senior Concierge Business 1.3.24

I need a professional business card to handout at networking events for my senior helper business. I would like to use the logo I have uploaded. The design should be clear and easy to read and should list the following information...
Delia Parkhurst
Owner
www.HarborlightElderAides.com
Cedar Hollow, Texas
936.482.5079
Delia@harborlightelderaides.com

Target Market(s)

Senior Citizens

Industry/Entity Type

Personal Helper/ Assisstant

Contact Information for Business Card

I have included the details in the project description box.

Font styles to use
Serif

Colors
0054AA
0677BA
7BADD7
CADEEF
E8F1F8
59FF00
82FF00
B8FF75
E3FFCB
F4FFEA
E54698
E96AAD
F1A4CE
F9D9EA
FCEFF6
6B429C
8869AF
B7A5CE
E3DAEB
F3F0F8

Requirements
Must have
• Include uploaded logo
Nice to have
• The log that has been uploaded
Should not have
• No crazy fonts

```html
<!DOCTYPE html>
<html lang="en">
<head>
<meta charset="utf-8">
<title>Harborlight Elder Aides – Business Card</title>
<link rel="stylesheet" href="https://fonts.googleapis.com/css2?family=Lato:wght@400;700&display=swap">
<style>
  :root {
    --stage: #2b2b2b;
    --card-white: #ffffff;
    --brand-purple: #642ee9;
    --accent-pink: #d9175f;
    --icon-teal: #168f94;
    --ink: #1a1a1a;
    --rule: #8a6ee6;
  }
  * { box-sizing: border-box; margin: 0; padding: 0; }
  html, body {
    width: 1047px; height: 1200px; overflow: hidden;
    background: var(--stage);
    font-family: "Lato", sans-serif;
  }
  .canvas { position: relative; width: 1047px; height: 1200px; }
  .card {
    position: absolute; left: 156px; width: 743px; height: 425px;
    border-radius: 20px; overflow: hidden;
  }
  .card--front { top: 120px; background: var(--card-white); }
  .card--back { top: 634px; background: var(--brand-purple); }

  .brand {
    position: absolute; display: flex; align-items: center; gap: 10px;
    font-weight: 400; white-space: nowrap;
  }
  .brand__dot { border-radius: 50%; flex: none; }
  .card--front .brand { right: 32px; top: 44px; font-size: 28px; color: var(--brand-purple); }
  .card--front .brand__dot { width: 18px; height: 18px; background: var(--brand-purple); }
  .card--back .brand {
    left: 0; right: 0; top: 185px; justify-content: center;
    font-size: 52px; color: var(--card-white);
  }
  .card--back .brand__dot { width: 34px; height: 34px; background: var(--card-white); }

  .person { position: absolute; left: 32px; top: 224px; }
  .person__name {
    font-size: 35px; font-weight: 700; color: var(--brand-purple);
    letter-spacing: 0.2px; line-height: 1.1;
  }
  .person__title { font-size: 20px; color: var(--accent-pink); margin-top: 2px; }

  .divider {
    position: absolute; left: 32px; right: 32px; top: 298px;
    height: 1px; background: var(--rule);
  }

  .contact { position: absolute; left: 32px; top: 315px; list-style: none; }
  .contact__item {
    display: flex; align-items: center; gap: 10px;
    font-size: 18px; color: var(--ink); height: 26px;
  }
  .contact__item:first-child { font-size: 20px; }
  .contact__icon { width: 18px; height: 18px; flex: none; }

  .location {
    position: absolute; right: 32px; top: 367px;
    font-size: 18px; line-height: 26px; color: var(--ink);
  }
</style>
</head>
<body>
<main class="canvas">
  <section class="card card--front">
    <div class="brand"><span class="brand__dot"></span>Harborlight Elder Aides</div>

    <div class="person">
      <h1 class="person__name">DELIA PARKHURST</h1>
      <p class="person__title">Owner</p>
    </div>

    <div class="divider"></div>

    <ul class="contact">
      <li class="contact__item">
        <svg class="contact__icon" viewBox="0 0 24 24" aria-hidden="true">
          <path fill="var(--icon-teal)" d="M6.6 10.8a15 15 0 0 0 6.6 6.6l2.2-2.2c.3-.3.7-.4 1-.2 1.1.4 2.3.6 3.6.6.6 0 1 .4 1 1V20c0 .6-.4 1-1 1A17 17 0 0 1 3 4c0-.6.4-1 1-1h3.5c.6 0 1 .4 1 1 0 1.3.2 2.5.6 3.6.1.3 0 .7-.2 1z"/>
        </svg>
        936.482.5079
      </li>
      <li class="contact__item">
        <svg class="contact__icon" viewBox="0 0 24 24" aria-hidden="true">
          <rect x="2" y="5" width="20" height="14" rx="1" fill="var(--icon-teal)"/>
          <path d="M3 6l9 7 9-7" fill="none" stroke="#fff" stroke-width="1.6"/>
        </svg>
        Delia@harborlightelderaides.com
      </li>
      <li class="contact__item">
        <svg class="contact__icon" viewBox="0 0 24 24" aria-hidden="true">
          <circle cx="12" cy="12" r="10" fill="var(--icon-teal)"/>
          <ellipse cx="12" cy="12" rx="4.5" ry="10" fill="none" stroke="#fff" stroke-width="1.4"/>
          <path d="M2 12h20" stroke="#fff" stroke-width="1.4"/>
        </svg>
        www.HarborlightElderAides.com
      </li>
    </ul>

    <p class="location">Cedar Hollow, Texas</p>
  </section>

  <section class="card card--back">
    <div class="brand"><span class="brand__dot"></span>Harborlight Elder Aides</div>
  </section>
</main>
</body>
</html>
```